Poster for a Bicycle show/Expo

We need a poster for a Bicycle show/Expo and sustainable transport. Exhibitors will sell bikes, cycling clothing, accessories, etc. ...
This show is annual and the Poster is for the 2015 edition.

The style must be modern, dynamic, bright colors.

Your concept must be compatible in a landscape format. (We will ourselves adaptations of different formats.)
Width: 210 mm
Height: 297 mm
It's necessary for us to have the source file (vector) for make, later, the different format (flyers, website, ...)

Content of the Poster:
- 1 big picture (no clip art)
- Big title: « Foire du Rayon » (« Salon » or « Salon du » can be small and « Vélo » big.)
- Subtitle: « et de la mobilité douce »
- Date: « 8, 9 et 10 mai 2015 » or « 8-10 mai 2015 »
- Place: « Halle TRV - Gare de Lunel »
- Text line 1: « www.foire-du-rayon.ch - Entrée gratuite »
- Text line 2« Piste d’essais - Restauration sur place »
- Text line 3: « Ve 8 mai de 17h à 21h - Sa 9 mai de 10h à 20h - Di 10 mai de 10h à 18h »
- Please, leave a zone in the poster for sponsors logos
(The predominant information (most visible) are: « Foire du Rayon » and « 8, 9 et 10 mai 2015 or 8-10 mai 2015 »)

Content of the big picture:
- from a cheap stock, like PixKiosk.com
- a bicycle in action or a detail of a bicycle (or a accessory) (no race bike)
- a modern picture with bright colors.
- if a person is on the picture, we prefer a men
- not an aerial view with cyclists in a landscape.

Some examples of poster of shows - with typo-title worked

http://www.expobassinlutece.com/Temp/IMG/F_a9b3c2d4e5f60718293a4b5c6d7e8f9012345678901_200_296.png

http://qx4m.tornafoire.fr/Data/pvtorn_mer/block/F_7cc1bb9396aef1d5e69283647561f0076457c357c5ea6.pdf
(page 2 of this PDF)

http://salons.rivol-evenements.fr/images/rivol-evenements/foires-salons/phototheque/salon-auto-bourlac/salon-auto-bourlac2012-affiche.jpg

http://www.tirovel.net/blog/wp-content/uploads/2007/03/affiche-salon-du-livre.jpg

http://www.quaimarin-gens.com/wp-content/affiche-cannes-2007.jpg
Updates

Hello,

For information, for your next versions, please, add the text "Piste d'essais".

- Text line 1: « www.foire-du-rayon.ch - Entrée gratuite »
- Text line 2: « Piste d’essais - Restauration sur place »
- Text line 3: « Ve 8 mai de 17h à 21h - Sa 9 mai de 10h à 20h - Di 10 mai de 10h à 18h »

Thanks,
Rodolphe

```html
<!DOCTYPE html>
<html lang="fr">
<head>
<meta charset="utf-8">
<title>Foire du Rayon et de la mobilité douce 2015</title>
<link rel="stylesheet" href="https://fonts.googleapis.com/css2?family=Arimo:wght@700&family=Open+Sans:wght@400&display=swap">
<style>
  :root {
    --photo-light: #d3d6de;
    --photo-mid: #8e94a3;
    --photo-dark: #2c303a;
    --photo-deep: #1c1f27;
    --title: #ffffff;
    --plum: #a04f8e;
    --orange: #f0892f;
    --band-text: #ffffff;
  }
  * { margin: 0; padding: 0; box-sizing: border-box; }
  html, body { width: 849px; height: 1200px; overflow: hidden; background: var(--photo-mid); }
  .poster { position: relative; width: 849px; height: 1200px; overflow: hidden; }
  .hero-photo {
    position: absolute; inset: 0;
    background:
      radial-gradient(ellipse 30% 22% at 50% 30%, rgba(58,63,76,0.75) 0%, rgba(58,63,76,0) 100%),
      radial-gradient(ellipse 60% 12% at 30% 8%, rgba(44,48,58,0.55) 0%, rgba(44,48,58,0) 100%),
      radial-gradient(ellipse 38% 26% at 12% 22%, #e4e6ec 0%, rgba(228,230,236,0) 100%),
      radial-gradient(ellipse 30% 20% at 85% 30%, #dfe2e8 0%, rgba(223,226,232,0) 100%),
      radial-gradient(ellipse 30% 38% at 6% 80%, var(--photo-deep) 0%, rgba(28,31,39,0) 100%),
      radial-gradient(ellipse 25% 30% at 88% 78%, #4a5060 0%, rgba(74,80,96,0) 100%),
      radial-gradient(ellipse 55% 20% at 40% 98%, #6a7082 0%, rgba(106,112,130,0) 100%),
      linear-gradient(165deg, var(--photo-light) 0%, var(--photo-mid) 50%, var(--photo-dark) 100%);
  }
  .title {
    position: absolute; right: 91px; top: 428px;
    font-family: "Arimo", "Helvetica Neue", Arial, sans-serif;
    font-weight: 700; color: var(--title);
    text-align: right; letter-spacing: -4px;
  }
  .title span { display: block; }
  .title-top { font-size: 160px; line-height: 140px; }
  .title-mid { font-size: 160px; line-height: 116px; }
  .title-main { font-size: 180px; line-height: 160px; }
  .info {
    position: absolute; right: 91px;
    font-family: "Open Sans", Arial, sans-serif; color: var(--band-text);
  }
  .subtitle {
    top: 865px; width: 430px; height: 41px;
    background: var(--plum); font-size: 25px; line-height: 41px;
    text-align: right; padding-right: 14px;
  }
  .dates-place {
    top: 918px; width: 540px; height: 38px;
    background: var(--plum); font-size: 18.5px; line-height: 38px;
    text-align: right; padding-right: 14px;
  }
  .practical, .hours {
    width: 270px; background: var(--orange);
    font-size: 18.5px; line-height: 22px;
    text-align: right; padding: 6px 12px 6px 10px;
  }
  .practical { top: 965px; height: 81px; }
  .hours { top: 1053px; height: 82px; }
</style>
</head>
<body>
<main class="poster">
  <div class="hero-photo" role="img" aria-label="Gros plan photographique d'une roue de vélo : rayons, frein à disque et cassette, tons gris bleutés"></div>

  <h1 class="title">
    <span class="title-top">Foire</span>
    <span class="title-mid">du</span>
    <span class="title-main">Rayon</span>
  </h1>

  <p class="info subtitle">et de la mobilité douce</p>
  <p class="info dates-place">8, 9 et 10 mai 2015 | Halle TRV - Gare de Lunel</p>
  <p class="info practical">www.foire-du-rayon.ch<br>Entrée gratuite<br>Restauration sur place</p>
  <p class="info hours">Ve 8 mai de 17h à 21h<br>Sa 9 mai de 10h à 20h<br>Di 10 mai de 10h à 18h</p>
</main>
</body>
</html>
```